Banner poster with different motifs

I'm looking for 5 banners and posters in A1 format in the same design, or the similarity must be recognizable...
Kept quite simple with different titles.

1 ballet
2 Contemporary Dance
3 high heels
4 Salsa & Bachata & Zouk
5 Hip Hop

Modern bright colors
it is for the entrance so that the students see here is a dance school

The text may also be included in the image
The photos are for guidance only; some are our own, some are purchased. However, we are permitted to use them, including our logo, of course.

```html
<!DOCTYPE html>
<html lang="en">
<head>
<meta charset="utf-8">
<title>High Heels – Movida Dance Center</title>
<link rel="stylesheet" href="https://fonts.googleapis.com/css2?family=Anton&family=Bebas+Neue&family=Montserrat:wght@300;400&family=Poppins:wght@400;700&display=swap">
<style>
  :root {
    --surround: #969696;
    --paper: #f1f1f3;
    --paper-light: #ffffff;
    --ray: #d9dae0;
    --floor: #e3e4e6;
    --navy: #222a48;
    --berry: #800f52;
    --ink: #1c1c22;
    --figure-dark: #1a1a1e;
    --figure-mid: #6c6c72;
  }
  html, body {
    margin: 0;
    width: 1027px;
    height: 1200px;
    overflow: hidden;
    background: var(--surround);
  }
  .poster {
    position: absolute;
    left: 128px;
    top: 55px;
    width: 771px;
    height: 1089px;
    overflow: hidden;
    background:
      radial-gradient(ellipse 55% 45% at 55% 45%, var(--paper-light) 0%, rgba(255,255,255,0) 70%),
      linear-gradient(180deg, var(--ray) 0%, var(--paper) 45%, var(--paper) 72%, var(--floor) 76%, var(--paper) 100%);
  }
  .poster__headline,
  .poster__footer {
    position: absolute;
    left: 0;
    top: 0;
    width: 771px;
    height: 1089px;
  }
  .headline__high {
    font-family: "Anton", sans-serif;
    fill: var(--navy);
  }
  .headline__heels {
    font-family: "Bebas Neue", sans-serif;
    fill: var(--berry);
  }
  .poster__photo {
    position: absolute;
    left: 43px;
    top: 530px;
    width: 728px;
    height: 430px;
    background:
      radial-gradient(ellipse 60% 45% at 55% 45%, rgba(26,26,30,0.55) 0%, rgba(108,108,114,0.25) 55%, rgba(255,255,255,0) 80%);
  }
  .brand__mark {
    fill: none;
    stroke: var(--ink);
    stroke-width: 1.4;
  }
  .brand__name {
    font-family: "Montserrat", sans-serif;
    font-weight: 300;
    font-size: 29px;
    fill: var(--ink);
  }
  .brand__tagline {
    font-family: "Montserrat", sans-serif;
    font-weight: 400;
    font-size: 8.5px;
    fill: var(--ink);
  }
  .web-address {
    font-family: "Poppins", sans-serif;
    font-weight: 400;
    font-size: 27px;
    fill: var(--ink);
  }
  .web-address__name {
    font-weight: 700;
    fill: var(--berry);
  }
</style>
</head>
<body>
  <main class="poster">
    <div class="poster__photo" role="img" aria-label="Photo of a dancer in a black glossy catsuit and platform high heels, leaning back over a white wooden chair"></div>

    <svg class="poster__headline" viewBox="0 0 771 1089" aria-label="High Heels">
      <text class="headline__high" x="162" y="272" font-size="254" textLength="449" lengthAdjust="spacingAndGlyphs">HIGH</text>
      <text class="headline__heels" transform="translate(158 740) scale(1 2.12)" x="0" y="0" font-size="300" textLength="453" lengthAdjust="spacingAndGlyphs">HEELS</text>
    </svg>

    <svg class="poster__footer" viewBox="0 0 771 1089">
      <circle class="brand__mark" cx="191" cy="940" r="26"/>
      <text class="brand__name" x="108" y="1007" textLength="167" lengthAdjust="spacing">MOVIDA</text>
      <text class="brand__tagline" x="108" y="1019" textLength="167" lengthAdjust="spacing">DANCE CENTER RIVERTON</text>
      <text class="web-address" x="343" y="1010" textLength="331" lengthAdjust="spacing">www.<tspan class="web-address__name">movida</tspan>.example</text>
    </svg>
  </main>
</body>
</html>
```